Card Design for my dog training business Brightpaw Obedience

Need a business card design for my dog training business with my new logo. Want the card to come off professional yet fun. Want it to be very eye catchy as well. I normally have these at vet clinics, pet stores, and groomers. so need it to look better than my competitors.
Target Market(s)
dog owners
Industry/Entity Type
Dog Training
Contact Information for Business Card
needs logo, my name and info
Font styles to use
Serif
Colors
0255a3
ffffff
ec1f27
000000
333333
fbfbfb
Requirements
Must have
- Brightpaw Obedience
- Felix Orland
- 415 903 2276
- info@brightpawobedience.example
- www.brightpawobedience.example

```html
<!DOCTYPE html>
<html lang="en">
<head>
<meta charset="utf-8">
<title>Brightpaw Obedience – Business Card</title>
<link href="https://fonts.googleapis.com/css2?family=EB+Garamond:ital,wght@0,500;1,400&family=Open+Sans:wght@400;700&display=swap" rel="stylesheet">
<style>
  :root {
    --backdrop: #2b2b2b;
    --card-dark: #1c1a1b;
    --card-light: #ffffff;
    --ink: #333333;
    --ink-strong: #1a1a1a;
    --rule: #9a9a9a;
    --paper-text: #fbfbfb;
  }
  * { box-sizing: border-box; margin: 0; padding: 0; }
  html, body { width: 1200px; height: 892px; overflow: hidden; }
  body { background: var(--backdrop); position: relative; font-family: "Open Sans", sans-serif; }

  .card { position: absolute; width: 540px; height: 309px; box-shadow: 0 12px 30px rgba(0,0,0,.45); }

  /* back side */
  .card-back { left: 70px; top: 120px; background: var(--card-dark); color: var(--paper-text); }
  .card-back .brand {
    position: absolute; left: 0; right: 0; top: 96px;
    display: flex; justify-content: center; align-items: center; gap: 12px;
    font-family: "EB Garamond", serif; font-weight: 500; font-size: 34px; letter-spacing: .5px;
  }
  .brand-dot { width: 14px; height: 14px; border-radius: 50%; background: var(--paper-text); }
  .card-back .tagline {
    position: absolute; left: 0; right: 0; bottom: 44px; text-align: center;
    font-family: "EB Garamond", serif; font-style: italic; font-size: 16px; letter-spacing: .3px;
  }

  /* front side */
  .card-front { left: 590px; top: 463px; background: var(--card-light); color: var(--ink); }
  .card-front .brand {
    position: absolute; right: 40px; top: 34px;
    display: flex; align-items: center; gap: 8px;
    font-family: "EB Garamond", serif; font-weight: 500; font-size: 22px; color: var(--ink-strong);
  }
  .card-front .brand .brand-dot { width: 10px; height: 10px; background: var(--ink-strong); }
  .top-rule { position: absolute; left: 0; right: 0; top: 118px; border-top: 1px solid var(--rule); }
  .holder {
    position: absolute; left: 32px; top: 178px;
    font-weight: 700; font-size: 20px; color: var(--ink-strong);
  }
  .name-rule { position: absolute; left: 32px; width: 200px; top: 212px; border-top: 1px solid var(--rule); }
  .contacts { position: absolute; left: 32px; top: 222px; list-style: none; font-size: 13.5px; line-height: 22px; }
  .contacts li { display: flex; align-items: center; gap: 10px; }
  .contacts svg { width: 13px; height: 13px; fill: var(--ink-strong); flex: none; }
</style>
</head>
<body>
  <section class="card card-back" aria-label="Card back">
    <div class="brand"><span class="brand-dot"></span>Brightpaw Obedience</div>
    <p class="tagline">“Building good habits with every walk we take.”</p>
  </section>

  <section class="card card-front" aria-label="Card front">
    <div class="brand"><span class="brand-dot"></span>Brightpaw Obedience</div>
    <div class="top-rule"></div>
    <h1 class="holder">Felix Orland</h1>
    <div class="name-rule"></div>
    <ul class="contacts">
      <li>
        <svg viewBox="0 0 16 16" aria-hidden="true"><path d="M1 5c0-2 2-3 7-3s7 1 7 3v1.5h-3.5V5h-7v1.5H1z"/><path d="M3 8h10l1 6H2z"/><circle cx="8" cy="11" r="1.6" fill="#fff"/></svg>
        415 903 2276
      </li>
      <li>
        <svg viewBox="0 0 16 16" aria-hidden="true"><path d="M1 3h14v10H1z"/><path d="M1 3l7 6 7-6" fill="none" stroke="#fff" stroke-width="1.4"/></svg>
        info@brightpawobedience.example
      </li>
      <li>
        <svg viewBox="0 0 16 16" aria-hidden="true"><circle cx="8" cy="8" r="7"/><path d="M1 8h14M8 1c-3 3.5-3 10.5 0 14M8 1c3 3.5 3 10.5 0 14" fill="none" stroke="#fff" stroke-width="1"/></svg>
        www.brightpawobedience.example
      </li>
    </ul>
  </section>
</body>
</html>
```